brovane business card

We are a commercial cleaning/janitorial service company our main target is building owners and managers.
Would like to see the icon as a background shadow in the front and the full logo in white on the back with a blue background.  On the card:
Dorn Hassel, Operations Manager, dorn@brovane-mail.com
48371-B Orchard Ln. 9 #402
Pellmont, OR 58217
555.304.8812, 800.555.4170

Updates
please include cell 555.618.2243
                                   
Thank you
If possible the fading logo on the front should be very subtle and light and lets look at centering that as well
thanks

Industry/Entity Type
Building
Look and feel
Each slider illustrates characteristics of the customer's brand and the style your logo design should communicate.

```html
<!DOCTYPE html>
<html lang="en">
<head>
<meta charset="utf-8">
<title>brovane business card</title>
<link rel="stylesheet" href="https://fonts.googleapis.com/css2?family=Arimo:wght@400;700&display=swap">
<style>
  :root {
    --page: #e6e7e9;
    --blue: #1f6db5;
    --blue-deep: #0e4f8f;
    --blue-light: #3d8fd6;
    --ink: #1c1c1e;
    --text-blue: #1a66b0;
    --white: #ffffff;
    --swoosh: #222326;
  }
  html, body {
    margin: 0;
    padding: 0;
    width: 1200px;
    height: 901px;
    overflow: hidden;
    background: var(--page);
    font-family: "Arimo", Arial, sans-serif;
  }
  .sheet {
    position: relative;
    width: 1200px;
    height: 901px;
  }
  .card {
    position: absolute;
    left: 250px;
    width: 700px;
    height: 400px;
    border-radius: 22px;
    overflow: hidden;
    box-shadow: 0 6px 18px rgba(0,0,0,0.18);
  }
  /* Back side */
  .card-back {
    top: 30px;
    background: radial-gradient(circle at 45% 40%, var(--blue-light) 0%, var(--blue) 45%, var(--blue-deep) 100%);
  }
  .back-brand {
    position: absolute;
    left: 0;
    right: 0;
    top: 160px;
    display: flex;
    justify-content: center;
    align-items: center;
    gap: 18px;
  }
  .back-brand .brand-dot {
    width: 66px;
    height: 66px;
    border-radius: 50%;
    background: var(--white);
  }
  .back-brand .brand-name {
    color: var(--white);
    font-weight: 700;
    font-size: 68px;
    letter-spacing: -1px;
    line-height: 1;
  }
  .back-web {
    position: absolute;
    right: 36px;
    bottom: 26px;
    color: var(--white);
    font-size: 17px;
  }
  /* Front side */
  .card-front {
    top: 471px;
    background: var(--white);
  }
  .card-front .wave {
    position: absolute;
    left: 0;
    top: 0;
    width: 700px;
    height: 400px;
  }
  .contact {
    position: absolute;
    left: 38px;
    top: 34px;
    font-size: 18px;
    color: var(--ink);
  }
  .address {
    color: var(--text-blue);
    line-height: 1.25;
    margin: 0 0 8px;
    font-style: normal;
  }
  .contact-list {
    list-style: none;
    margin: 0;
    padding: 0;
  }
  .contact-list li {
    display: flex;
    align-items: center;
    gap: 10px;
    height: 26px;
  }
  .contact-list svg {
    width: 17px;
    height: 17px;
    flex: none;
  }
  .front-brand {
    position: absolute;
    right: 48px;
    top: 92px;
    display: flex;
    align-items: center;
    gap: 12px;
  }
  .front-brand .brand-dot {
    width: 44px;
    height: 44px;
    border-radius: 50%;
    background: var(--blue);
  }
  .front-brand .brand-name {
    color: var(--blue);
    font-weight: 700;
    font-size: 48px;
    letter-spacing: -1px;
    line-height: 1;
  }
  .person {
    position: absolute;
    right: 56px;
    top: 302px;
    color: var(--white);
    text-align: center;
  }
  .person-name {
    font-weight: 700;
    font-size: 22px;
    font-variant: small-caps;
    letter-spacing: 0.5px;
    margin: 0;
  }
  .person-role {
    font-size: 16px;
    margin: 4px 0 0;
  }
</style>
</head>
<body>
<main class="sheet">

  <section class="card card-back" aria-label="Card back">
    <div class="back-brand">
      <span class="brand-dot"></span>
      <span class="brand-name">brovane</span>
    </div>
    <div class="back-web">www.brovane-co.com</div>
  </section>

  <section class="card card-front" aria-label="Card front">
    <svg class="wave" viewBox="0 0 700 400" aria-hidden="true">
      <defs>
        <linearGradient id="band" x1="0" y1="0" x2="0" y2="1">
          <stop offset="0" stop-color="#2a7fcc"/>
          <stop offset="1" stop-color="#135d9f"/>
        </linearGradient>
      </defs>
      <path d="M0,228 C170,236 330,296 700,276 L700,400 L0,400 Z" fill="url(#band)"/>
      <path d="M0,200 C190,212 340,272 560,268 C620,267 670,262 700,258 C660,270 600,276 540,277 C330,282 180,226 0,216 Z" fill="var(--swoosh)"/>
    </svg>

    <div class="contact">
      <address class="address">48371-B Orchard Ln. 9 #402<br>Pellmont, OR 58217</address>
      <ul class="contact-list">
        <li>
          <svg viewBox="0 0 20 20"><circle cx="10" cy="10" r="10" fill="var(--blue)"/><path d="M5 8c0-2 2-3 5-3s5 1 5 3l-2 1-1-2H8L7 9 5 8zM7 10h6l1 4H6z" fill="#fff"/></svg>
          <span>555.304.8812, 800.555.4170</span>
        </li>
        <li>
          <svg viewBox="0 0 20 20"><circle cx="10" cy="10" r="10" fill="var(--blue)"/><rect x="7" y="4" width="6" height="12" rx="1" fill="#fff"/><rect x="8" y="5.5" width="4" height="7" fill="var(--blue)"/></svg>
          <span>555.618.2243</span>
        </li>
        <li>
          <svg viewBox="0 0 20 20"><circle cx="10" cy="10" r="10" fill="var(--blue)"/><rect x="4.5" y="6" width="11" height="8" fill="#fff"/><path d="M4.5 6l5.5 4.5L15.5 6" fill="none" stroke="var(--blue)" stroke-width="1.2"/></svg>
          <span>dorn@brovane-mail.com</span>
        </li>
        <li>
          <svg viewBox="0 0 20 20"><circle cx="10" cy="10" r="10" fill="var(--blue)"/><circle cx="10" cy="10" r="5.5" fill="none" stroke="#fff" stroke-width="1.3"/><ellipse cx="10" cy="10" rx="2.3" ry="5.5" fill="none" stroke="#fff" stroke-width="1.1"/><path d="M4.5 10h11" stroke="#fff" stroke-width="1.1"/></svg>
          <span>www.brovane-co.com</span>
        </li>
      </ul>
    </div>

    <div class="front-brand">
      <span class="brand-dot"></span>
      <span class="brand-name">brovane</span>
    </div>

    <div class="person">
      <p class="person-name">Dorn Hassel</p>
      <p class="person-role">Operations Manager</p>
    </div>
  </section>

</main>
</body>
</html>
```